Halberd Guard Services

Our Company is a security business which needs a cut edge design, the final product should have all relevant information and maintain a bold but modern and professional look.

Target Market(s)

A cut edge design which will attract any audience

Industry/Entity Type

Security

Contact Information for Business Card

HALBERD GUARD SERVICES

Gregor Lindqvist
Operations Manager
Phone: 0491 735 219

Email: info@halberdguard.com.au
Web: www.halberdguard.com.au

Requirements
Must have
• Must be double sided and contain all relevant information and the company logo.

```html
<!DOCTYPE html>
<html lang="en">
<head>
<meta charset="utf-8">
<title>Halberd Guard Services – Business Card</title>
<link href="https://fonts.googleapis.com/css2?family=Open+Sans:wght@400;600;800&display=swap" rel="stylesheet">
<style>
  :root {
    --bg: #e6e8e9;
    --card-front: #ffffff;
    --card-front-shade: #eceeef;
    --card-back: #4f6e75;
    --slate-dark: #34494f;
    --slate-mark: #3d565c;
    --ink: #2b2f31;
    --white: #ffffff;
    --accent: #f5a21c;
  }
  * { margin: 0; padding: 0; box-sizing: border-box; }
  html, body {
    width: 1200px;
    height: 951px;
    overflow: hidden;
    background: var(--bg);
    font-family: "Open Sans", Arial, sans-serif;
  }
  .canvas { position: relative; width: 1200px; height: 951px; }
  .card {
    position: absolute;
    left: 230px;
    width: 740px;
    height: 423px;
    border-radius: 26px;
    overflow: hidden;
    box-shadow: 0 10px 28px rgba(0, 0, 0, 0.18);
  }
  .card--front {
    top: 40px;
    background: radial-gradient(ellipse at 45% 40%, var(--card-front) 40%, var(--card-front-shade) 100%);
  }
  .card--back { top: 488px; background: var(--card-back); }

  /* front side */
  .front-mark {
    position: absolute;
    left: 0; right: 0; top: 92px;
    display: flex; flex-direction: column; align-items: center;
  }
  .mark-circle {
    width: 96px; height: 96px;
    border-radius: 50%;
    background: var(--slate-dark);
  }
  .front-name {
    margin-top: 20px;
    font-weight: 800;
    font-size: 50px;
    letter-spacing: 1px;
    color: var(--slate-dark);
    line-height: 1;
  }
  .front-web {
    position: absolute;
    left: 0; right: 0; bottom: 62px;
    text-align: center;
    font-weight: 600;
    font-size: 24px;
    letter-spacing: 2px;
    color: var(--ink);
  }

  /* back side */
  .back-mark {
    position: absolute;
    left: 40px; top: 120px;
    width: 300px;
    display: flex; flex-direction: column; align-items: center;
  }
  .back-mark .mark-circle { width: 88px; height: 88px; background: var(--slate-mark); }
  .back-name {
    margin-top: 18px;
    font-weight: 800;
    font-size: 34px;
    color: var(--slate-mark);
    line-height: 1;
    white-space: nowrap;
  }
  .contact {
    position: absolute;
    right: 52px; top: 60px;
    text-align: right;
    color: var(--white);
  }
  .contact__person { font-size: 27px; line-height: 1.2; }
  .contact__role { font-size: 17px; color: var(--accent); margin-bottom: 96px; }
  .contact__line { font-size: 20px; line-height: 1.35; }
  .contact__web-name { color: var(--accent); }
  .edge-tab {
    position: absolute;
    right: 0; top: 128px;
    width: 10px; height: 90px;
    background: var(--accent);
  }
</style>
</head>
<body>
<main class="canvas">
  <section class="card card--front" aria-label="Business card front">
    <div class="front-mark">
      <div class="mark-circle"></div>
      <div class="front-name">HALBERD GUARD</div>
    </div>
    <p class="front-web">www.halberdguard.com.au</p>
  </section>

  <section class="card card--back" aria-label="Business card back">
    <div class="back-mark">
      <div class="mark-circle"></div>
      <div class="back-name">HALBERD GUARD</div>
    </div>
    <div class="contact">
      <p class="contact__person">Gregor Lindqvist</p>
      <p class="contact__role">Operations Manager</p>
      <p class="contact__line">0491 735 219</p>
      <p class="contact__line">info@halberdguard.com.au</p>
      <p class="contact__line">www.<span class="contact__web-name">halberdguard</span>.com.au</p>
    </div>
    <div class="edge-tab"></div>
  </section>
</main>
</body>
</html>
```